Business Card Design needed for start up company Halvora

In need of a new business card designed for a start up company based in Sydney, Halvora is a new start up innovative Company, our mission it to make property accessible for everyday Australian and to become the leading Real Estate platform in Australia. We want it to be fresh and clean.

Industry/Entity Type

Financial

Contact Information for Business Card

Section for Name
Section for Title

HALVORA - The Strength of Pooling
Mobile:
Direct:

Font styles to use
Sans Serif

Colors
33a6d7
0692cd
0255a3
ffffff

Requirements
Must have
• Logo, all business card details

```html
<!DOCTYPE html>
<html lang="en">
<head>
<meta charset="utf-8">
<title>Halvora — Business Card</title>
<link href="https://fonts.googleapis.com/css2?family=Open+Sans:wght@400;600;700&display=swap" rel="stylesheet">
<style>
  :root {
    --sky: #33a6d7;
    --aqua: #2fd0e6;
    --blue: #0692cd;
    --navy: #0255a3;
    --ink: #4a4f57;
    --white: #ffffff;
    --page: #e9ecef;
  }
  * { box-sizing: border-box; margin: 0; padding: 0; }
  html, body {
    width: 1200px; height: 900px; overflow: hidden;
    background: var(--page);
    font-family: "Open Sans", sans-serif;
  }
  .stage {
    width: 1200px; height: 900px;
    display: flex; flex-direction: column; align-items: center; justify-content: center;
    gap: 56px;
  }
  .card {
    position: relative;
    width: 660px; height: 377px;
    border-radius: 3px;
    box-shadow: 0 10px 28px rgba(0,0,0,.14);
    overflow: hidden;
  }
  .card-front {
    background: linear-gradient(110deg, var(--aqua) 0%, var(--sky) 45%, var(--blue) 100%);
    display: flex; flex-direction: column; align-items: center; justify-content: center;
    color: var(--white);
  }
  .wordmark {
    font-weight: 600; line-height: 1; letter-spacing: 0;
  }
  .card-front .wordmark { font-size: 60px; color: var(--white); }
  .tagline { margin-top: 26px; font-size: 15px; font-weight: 400; }

  .card-back { background: var(--white); }
  .card-back .wordmark {
    position: absolute; left: 48px; top: 128px;
    font-size: 54px; color: var(--navy);
  }
  .contact {
    position: absolute; left: 462px; top: 58px;
    list-style: none; font-size: 13px; color: var(--ink); line-height: 1.5;
  }
  .contact li { display: flex; align-items: center; gap: 8px; }
  .contact .address { display: block; margin-bottom: 4px; }
  .contact svg { width: 12px; height: 12px; fill: var(--navy); flex: none; }
  .person { position: absolute; left: 48px; bottom: 62px; }
  .person-name { font-size: 17px; font-weight: 700; color: var(--navy); letter-spacing: .3px; }
  .person-title { font-size: 16px; font-weight: 400; color: var(--blue); }
  .footer-band { position: absolute; left: 0; right: 0; bottom: 0; height: 14px; }
  .band-navy { position: absolute; left: 0; bottom: 0; width: 68%; height: 14px; background: var(--navy); }
  .band-sky { position: absolute; right: 0; top: 0; width: calc(32% - 6px); height: 8px; background: var(--blue); }
</style>
</head>
<body>
<main class="stage">
  <section class="card card-front" aria-label="Card front">
    <p class="wordmark">Halvora</p>
    <p class="tagline">The Strength of Pooling</p>
  </section>

  <section class="card card-back" aria-label="Card back">
    <p class="wordmark">Halvora</p>
    <ul class="contact">
      <li class="address">42 Harbourview Street<br>Sydney, NSW 2000</li>
      <li><svg viewBox="0 0 12 12"><path d="M2 1h2l1 3-1.3 1a7 7 0 0 0 3.3 3.3L8 7l3 1v2a1 1 0 0 1-1 1A9 9 0 0 1 1 2a1 1 0 0 1 1-1z"/></svg>02 9481 6620</li>
      <li><svg viewBox="0 0 12 12"><path d="M3.5 0h5a1 1 0 0 1 1 1v10a1 1 0 0 1-1 1h-5a1 1 0 0 1-1-1V1a1 1 0 0 1 1-1zm.5 1.5v8h4v-8z"/></svg>0412 735 908</li>
      <li><svg viewBox="0 0 12 12"><path d="M0 2.5h12v7H0zM.8 3l5.2 3.6L11.2 3z" fill-rule="evenodd"/></svg>elise@halvora.com.au</li>
      <li><svg viewBox="0 0 12 12"><circle cx="6" cy="6" r="5.5"/></svg>www.halvora.com.au</li>
    </ul>
    <div class="person">
      <p class="person-name">ELISE MARKHAM</p>
      <p class="person-title">CEO/FOUNDER</p>
    </div>
    <div class="footer-band"><span class="band-navy"></span><span class="band-sky"></span></div>
  </section>
</main>
</body>
</html>
```